Business card design needed

I run a Beautician studio (for 7 years now)
I offer
- Velmo Body Sugaring
- Ruby Glaze
- Nails
- Facials
- Manicure
- Foot Treatment
It might not be necessary to list all those treatments?
Maybe the link to the Website is sufficient?
I leave that up to you ...
(more info on www.FernAndDewByLenka.com.au)
Velmo BodySugaring is our biggest success, It replaces waxing.
I would like to incorporate the logo into the Business Card.
We had many complaints regarding our old Business Cards as the Phone Number was to small.
On the backside, we would like a "your next Appointment" section.
Looking forward to you Design, cheers ... Lenka
Industry/Entity Type
Business
Contact Information for Business Card
Fern by Dew by Lenka
14 Korrin Sqr 3942 Lorrendale
www.FernAndDewByLenka.com.au
03 9481 2267

```html
<!DOCTYPE html>
<html lang="en">
<head>
<meta charset="utf-8">
<title>Velmo Body Sugaring – Business Cards</title>
<link rel="stylesheet" href="https://fonts.googleapis.com/css2?family=Open+Sans:wght@400;600;700&family=Libre+Baskerville&display=swap">
<style>
  :root {
    --backdrop: #1c1c1c;
    --card: #ffffff;
    --ink: #333333;
    --ink-soft: #4a4a4a;
    --rule: #555555;
    --leaf-green: #1f6b2e;
    --sun: #f0a020;
    --ghost: #f3f4f0;
  }
  * { box-sizing: border-box; margin: 0; padding: 0; }
  html, body {
    width: 1200px; height: 728px; overflow: hidden;
    background: var(--backdrop);
    font-family: "Open Sans", Arial, sans-serif;
    color: var(--ink);
  }
  .stage { position: relative; width: 1200px; height: 728px; }
  .card {
    position: absolute; width: 542px; height: 308px;
    background: var(--card); overflow: hidden;
  }
  .card--contact { left: 41px; top: 37px; }
  .card--appointment-a { left: 614px; top: 37px; }
  .card--hours { left: 43px; top: 380px; }
  .card--appointment-b { left: 624px; top: 384px; }
  .abs { position: absolute; white-space: nowrap; }

  /* brand mark stand-in */
  .brand {
    position: absolute; display: flex; flex-direction: column;
    align-items: center; justify-content: center; gap: 12px;
  }
  .brand__dot { width: 72px; height: 72px; border-radius: 50%; background: var(--sun); }
  .brand__name {
    font-size: 24px; font-weight: 400; letter-spacing: 2px; color: var(--ink);
    white-space: nowrap;
  }
  .brand--small { gap: 6px; }
  .brand--small .brand__dot { width: 36px; height: 36px; }
  .brand--small .brand__name { font-size: 9px; letter-spacing: 0.5px; }
  .card--contact .brand { left: 100px; top: 10px; width: 342px; height: 150px; }
  .card--hours .brand { left: 100px; top: 10px; width: 342px; height: 170px; }

  /* contact card */
  .studio-name { right: 312px; top: 190px; font-size: 17px; font-weight: 600; color: var(--ink); }
  .studio-address { right: 312px; top: 217px; font-size: 13px; color: var(--ink-soft); }
  .divider { left: 242px; top: 182px; width: 1px; height: 63px; background: #bbbbbb; }
  .contact-line { left: 254px; display: flex; align-items: center; gap: 6px; }
  .contact-line--phone { top: 188px; font-size: 17px; }
  .contact-line--web { top: 216px; font-size: 14px; }
  .contact-line svg { flex: none; }
  .treatments-title {
    left: 0; width: 100%; top: 250px; text-align: center;
    font-size: 15px; font-weight: 700; letter-spacing: 1px;
  }
  .treatments-list {
    left: 0; width: 100%; top: 273px; text-align: center; font-size: 13px;
  }

  /* hours card */
  .hours-web {
    left: 0; width: 100%; top: 190px; text-align: center;
    font-size: 14px; letter-spacing: 2.2px;
  }
  .hours-title {
    left: 0; width: 100%; top: 222px; text-align: center;
    font-size: 20px; font-weight: 700; letter-spacing: 1.5px; color: var(--ink-soft);
  }
  .hours-times {
    left: 0; width: 100%; top: 260px; text-align: center;
    font-size: 15.5px; font-weight: 600; color: var(--ink-soft);
  }
  .hours-times .sep { color: #aaaaaa; margin: 0 8px; font-weight: 400; }

  /* appointment cards */
  .appt-heading {
    left: 37px; top: 52px; font-family: "Libre Baskerville", Georgia, serif;
    font-size: 17px; font-weight: 400; color: var(--leaf-green); letter-spacing: 0.5px;
  }
  .appt-label { font-size: 15px; color: var(--ink); }
  .appt-line { position: absolute; height: 0; border-bottom: 1px solid var(--rule); }
  .appt-line--dotted { border-bottom: 1px dotted #777777; }
  .appt-box { position: absolute; border: 1px solid var(--rule); height: 20px; }
  .appt-day { font-size: 15px; font-weight: 600; color: var(--ink-soft); }
  .appt-note { left: 31px; top: 250px; width: 460px; white-space: normal; font-size: 13px; line-height: 19px; color: var(--ink); }
  .card--appointment-a .brand { left: 368px; top: 14px; width: 100px; height: 86px; }
  .ghost-name {
    left: 0; width: 100%; top: 188px; text-align: center;
    font-size: 64px; font-weight: 400; letter-spacing: 6px; color: var(--ghost);
  }
</style>
</head>
<body>
<main class="stage">

  <section class="card card--contact">
    <div class="brand">
      <span class="brand__dot"></span>
      <span class="brand__name">Velmo Body Sugaring</span>
    </div>
    <p class="abs studio-name">Fern by Dew by Lenka</p>
    <p class="abs studio-address">14 Korrin Sqr 3942 Lorrendale</p>
    <span class="abs divider"></span>
    <p class="abs contact-line contact-line--phone">
      <svg width="16" height="16" viewBox="0 0 16 16" aria-hidden="true">
        <circle cx="8" cy="8" r="7.5" fill="#2e8b3a"/>
        <path d="M5.2 4.2l1.4-.3.9 2-.9.7c.5 1.1 1.3 1.9 2.4 2.4l.7-.9 2 .9-.3 1.4c-3.4.2-6.4-2.8-6.2-6.2z" fill="#fff"/>
      </svg>
      03 9481 2267
    </p>
    <p class="abs contact-line contact-line--web">
      <svg width="14" height="14" viewBox="0 0 14 14" aria-hidden="true">
        <circle cx="7" cy="7" r="6.5" fill="#2e8b3a"/>
        <path d="M.8 7h12.4M7 .6v12.8M7 .6c-3 3.5-3 9.3 0 12.8M7 .6c3 3.5 3 9.3 0 12.8" stroke="#fff" stroke-width=".9" fill="none"/>
      </svg>
      www.FernAndDewByLenka.com.au
    </p>
    <p class="abs treatments-title">Treatments offerd</p>
    <p class="abs treatments-list">• Velmo Body Sugaring &nbsp;• Ruby Glaze &nbsp;• Nails &nbsp;• Facials &nbsp;• Manicure &nbsp;• Foot Treatment</p>
  </section>

  <section class="card card--appointment-a">
    <div class="brand brand--small">
      <span class="brand__dot"></span>
      <span class="brand__name">Velmo Body Sugaring</span>
    </div>
    <h2 class="abs appt-heading">YOUR APPOINTMENT</h2>
    <span class="abs appt-label" style="left:37px;top:90px">Name :</span>
    <span class="appt-line appt-line--dotted" style="left:97px;top:105px;width:290px"></span>
    <span class="abs appt-label" style="left:37px;top:128px">Date :</span>
    <span class="appt-line" style="left:98px;top:143px;width:98px"></span>
    <span class="abs appt-label" style="left:201px;top:128px">Time :</span>
    <span class="appt-line" style="left:247px;top:143px;width:93px"></span>
    <span class="abs appt-label" style="left:342px;top:128px">am / pm</span>
    <span class="abs appt-label" style="left:37px;top:166px">Next Appointment</span>
    <span class="appt-box" style="left:182px;top:167px;width:98px"></span>
    <span class="appt-box" style="left:311px;top:167px;width:98px"></span>
    <span class="abs appt-day" style="left:33px;top:204px">MON</span>
    <span class="appt-box" style="left:78px;top:204px;width:35px"></span>
    <span class="abs appt-day" style="left:120px;top:204px">TUE</span>
    <span class="appt-box" style="left:158px;top:204px;width:34px"></span>
    <span class="abs appt-day" style="left:199px;top:204px">WED</span>
    <span class="appt-box" style="left:243px;top:204px;width:33px"></span>
    <span class="abs appt-day" style="left:283px;top:204px">THU</span>
    <span class="appt-box" style="left:324px;top:204px;width:32px"></span>
    <span class="abs appt-day" style="left:364px;top:204px">FRI</span>
    <span class="appt-box" style="left:395px;top:204px;width:33px"></span>
    <span class="abs appt-day" style="left:437px;top:204px">SAT</span>
    <span class="appt-box" style="left:472px;top:204px;width:33px"></span>
    <p class="abs appt-note">It would be appreciated if 24 hours notice could be given if you are unable to attend an appointment</p>
  </section>

  <section class="card card--hours">
    <div class="brand">
      <span class="brand__dot"></span>
      <span class="brand__name">Velmo Body Sugaring</span>
    </div>
    <p class="abs hours-web">www.FernAndDewByLenka.com.au</p>
    <h2 class="abs hours-title">Hours of Operation</h2>
    <p class="abs hours-times">Mon - Fri: 7.30am - 7.00pm<span class="sep">|</span>Saturday: 7.30am - 12.00pm</p>
  </section>

  <section class="card card--appointment-b">
    <p class="abs ghost-name" aria-hidden="true">Velmo</p>
    <h2 class="abs appt-heading">YOUR APPOINTMENT</h2>
    <span class="abs appt-label" style="left:37px;top:90px">Name :</span>
    <span class="appt-line appt-line--dotted" style="left:97px;top:105px;width:290px"></span>
    <span class="abs appt-label" style="left:37px;top:128px">Date :</span>
    <span class="appt-line" style="left:98px;top:143px;width:98px"></span>
    <span class="abs appt-label" style="left:201px;top:128px">Time :</span>
    <span class="appt-line" style="left:247px;top:143px;width:93px"></span>
    <span class="abs appt-label" style="left:342px;top:128px">am / pm</span>
    <span class="abs appt-label" style="left:37px;top:166px">Next Appointment</span>
    <span class="appt-box" style="left:182px;top:167px;width:98px"></span>
    <span class="appt-box" style="left:311px;top:167px;width:98px"></span>
    <span class="abs appt-day" style="left:33px;top:204px">MON</span>
    <span class="appt-box" style="left:78px;top:204px;width:35px"></span>
    <span class="abs appt-day" style="left:120px;top:204px">TUE</span>
    <span class="appt-box" style="left:158px;top:204px;width:34px"></span>
    <span class="abs appt-day" style="left:199px;top:204px">WED</span>
    <span class="appt-box" style="left:243px;top:204px;width:33px"></span>
    <span class="abs appt-day" style="left:283px;top:204px">THU</span>
    <span class="appt-box" style="left:324px;top:204px;width:32px"></span>
    <span class="abs appt-day" style="left:364px;top:204px">FRI</span>
    <span class="appt-box" style="left:395px;top:204px;width:33px"></span>
    <span class="abs appt-day" style="left:437px;top:204px">SAT</span>
    <span class="appt-box" style="left:472px;top:204px;width:33px"></span>
    <p class="abs appt-note">It would be appreciated if 24 hours notice could be given if you are unable to attend an appointment</p>
  </section>

</main>
</body>
</html>
```